Professional Website for Leading Global Private Equity Real Estate Company

The company is a leading global Private Equity Real Estate (PERE). We need a homepage design, an inner page design, and color/font tweaks to the logo (color should be more soothing than current blue used in the logo). The logo website should project the company as global, professional, experienced, trustworthy, accessible, YOUNG, DYNAMIC, hi-tech. PLEASE SEE the attached Design Brief Word Doc for details.

Target Market(s)

institional investors and wealthy private individuals

Industry/Entity Type

Finance

Number of Pages Required

2 page

Font styles to use
Sans Serif
Other font styles liked:
• either like in https://www.ferndalequay.com/ or like in presentations (Montserrat Black & Montserrat Light, Century Gothic, Blair ITC, Almoni Neue DL 4.0 AAA Medium, Almoni DL AAA)

Requirements
Must have
• new color palette that is NOT based on current logo. they want a more soothing color palette than the blue in that logo. the new color palette should project: global, professional, experienced, trustworthy, accessible, YOUNG, DYNAMIC, hi-tech.
Nice to have
• the likes these sites: https://www.ferndalequay.com/ and https://www.tvr.law/

```html
<!DOCTYPE html>
<html lang="en">
<head>
<meta charset="utf-8">
<title>Veloren Real Estate</title>
<link href="https://fonts.googleapis.com/css2?family=Michroma&family=Roboto:wght@300;400;500&display=swap" rel="stylesheet">
<style>
:root{
  --navy:#1e3457;
  --navy-deep:#10244a;
  --navy-bar:#0c1d3d;
  --accent:#3d5f92;
  --ink:#2c2f36;
  --muted:#555b66;
  --paper:#f2f3f5;
  --white:#ffffff;
}
*{margin:0;padding:0;box-sizing:border-box}
html,body{width:1200px;height:4184px;overflow:hidden}
body{position:relative;background:var(--white);font-family:'Roboto',Arial,sans-serif;color:var(--ink)}
.abs{position:absolute}
h1,h2,h3,h4{font-weight:400}
.display{font-family:'Michroma',Arial,sans-serif;text-transform:uppercase;letter-spacing:.5px}
.center{left:0;width:1200px;text-align:center}
.rule{height:3px;background:var(--accent);width:58px}
.link{font-family:'Michroma',Arial,sans-serif;text-transform:uppercase;color:var(--accent);text-decoration:underline;font-size:11px}

/* hero */
.hero{top:0;left:0;width:1200px;height:700px;
  background:
    radial-gradient(ellipse 520px 70px at 560px 150px,rgba(232,170,80,.55),transparent 70%),
    radial-gradient(ellipse 300px 60px at 980px 170px,rgba(220,150,90,.35),transparent 70%),
    radial-gradient(ellipse 260px 90px at 430px 560px,rgba(70,90,230,.45),transparent 70%),
    radial-gradient(ellipse 360px 120px at 760px 470px,rgba(240,200,150,.28),transparent 70%),
    radial-gradient(ellipse 420px 160px at 150px 420px,rgba(120,110,150,.35),transparent 70%),
    radial-gradient(ellipse 300px 130px at 1050px 520px,rgba(160,120,170,.3),transparent 70%),
    linear-gradient(180deg,#2c3150 0%,#53506a 10%,#8a6a55 20%,#4f5670 34%,#3a4260 55%,#2c3350 78%,#1e2439 100%)}
.hero::after{content:"";position:absolute;inset:0;background:linear-gradient(180deg,rgba(10,16,32,.35) 0%,rgba(10,16,32,.1) 30%,rgba(10,16,32,.15) 100%)}
.nav{top:19px;left:0;width:1200px;height:36px;z-index:2;color:var(--white)}
.brand{left:46px;top:0;height:36px;display:flex;align-items:center;gap:10px;font-size:21px;font-weight:400;letter-spacing:.5px;white-space:nowrap}
.brand-dot{width:34px;height:34px;border-radius:50%;background:var(--white)}
.nav-item{top:10px;font-size:12.5px;font-weight:500;white-space:nowrap}
.login{left:1046px;top:0;width:99px;height:35px;border:1.5px solid var(--white);border-radius:18px;font-size:12px;display:flex;align-items:center;justify-content:center}
.play{left:582px;top:226px;width:54px;height:54px;border:2px solid var(--white);border-radius:50%;z-index:2}
.hero-title{top:297px;font-size:33px;line-height:43px;color:var(--white);z-index:2}
.hero-link{top:406px;font-size:17px;color:var(--white);z-index:2;text-decoration:underline}

/* who we are */
.who{top:700px;left:0;width:1200px;height:529px;
  background:
    radial-gradient(ellipse 200px 240px at 1080px 380px,rgba(150,155,165,.35),transparent 70%),
    radial-gradient(ellipse 240px 200px at 120px 420px,rgba(150,155,165,.35),transparent 70%),
    linear-gradient(180deg,#f8f8f9 0%,#eff0f2 25%,#d9dce0 55%,#b9bdc4 100%)}
.eyebrow{top:774px;font-size:11px;color:var(--accent)}
.who-title{top:794px;font-size:26px;line-height:32px;color:#333}
.who-copy{top:856px;left:230px;width:740px;text-align:center;font-size:14.5px;line-height:23px;color:var(--muted)}
.who-mark{left:574px;top:932px;width:56px;height:56px;border-radius:50%;background:var(--accent)}
.stat{width:300px;text-align:center}
.stat-num{font-size:40px;line-height:50px;color:var(--navy);-webkit-text-stroke:1px var(--navy)}
.stat-label{font-size:15px;color:#444;margin-top:4px;letter-spacing:.3px}

/* platforms */
.plat-title{top:1302px;font-size:26px;line-height:32px;color:#333}
.plat{width:210px;text-align:center}
.plat-photo{width:194px;height:194px;border-radius:50%;margin:0 auto}
.plat-name{margin-top:28px;font-size:12.5px;line-height:19px;color:#222;-webkit-text-stroke:.3px #222}
.plat-copy{margin-top:10px;font-size:12px;line-height:20.5px;color:var(--muted)}
.plat .link{display:block;margin-top:18px}

/* edge */
.edge{top:1890px;left:0;width:1200px;height:522px;background:var(--paper)}
.edge-photo{top:1890px;left:0;width:656px;height:522px;
  background:
    radial-gradient(ellipse 30px 260px at 300px 330px,rgba(90,90,90,.75),transparent 75%),
    radial-gradient(ellipse 90px 160px at 420px 420px,rgba(40,40,40,.85),transparent 80%),
    radial-gradient(ellipse 200px 140px at 120px 430px,rgba(70,70,70,.7),transparent 80%),
    linear-gradient(180deg,#f4f4f4 0%,#e2e2e2 30%,#a9a9a9 60%,#5a5a5a 85%,#3a3a3a 100%);
  clip-path:polygon(0 0,656px 0,460px 522px,0 522px)}
.section-title{font-size:26px;line-height:32px;color:#222}
.body-copy{font-size:15px;line-height:27px;color:#444}

/* newsletter */
.news{top:2412px;left:0;width:1200px;height:385px;
  background:
    radial-gradient(ellipse 120px 260px at 1020px 300px,rgba(20,35,65,.6),transparent 75%),
    radial-gradient(ellipse 160px 220px at 140px 320px,rgba(60,85,125,.45),transparent 75%),
    linear-gradient(180deg,#2f4870 0%,#243c62 45%,#1c3154 100%)}
.news-title{top:2500px;font-size:27px;line-height:32px;color:var(--white)}
.news-sub{top:2552px;font-size:17px;color:#e7ebf2}
.news-input{left:334px;top:2598px;width:400px;height:54px;background:var(--white);border-radius:27px 0 0 27px;font-size:14px;color:#777;padding:19px 0 0 30px}
.news-btn{left:721px;top:2598px;width:140px;height:54px;background:var(--accent);border-radius:0 27px 27px 0;color:var(--white);font-size:12px;display:flex;align-items:center;justify-content:center}

/* responsibility */
.resp-photo{top:2797px;left:554px;width:646px;height:496px;
  background:
    radial-gradient(ellipse 110px 170px at 220px 240px,rgba(40,40,40,.8),transparent 75%),
    radial-gradient(ellipse 90px 150px at 420px 220px,rgba(30,30,30,.85),transparent 75%),
    radial-gradient(ellipse 100px 160px at 560px 230px,rgba(60,60,60,.7),transparent 75%),
    radial-gradient(ellipse 130px 60px at 360px 320px,rgba(220,220,220,.7),transparent 75%),
    linear-gradient(180deg,#dcdcdc 0%,#b2b2b2 35%,#6f6f6f 70%,#3c3c3c 100%);
  clip-path:polygon(0 0,646px 0,646px 496px,185px 496px)}

/* contact */
.contact{top:3293px;left:0;width:1200px;height:519px;
  background:
    radial-gradient(ellipse 160px 220px at 100px 160px,rgba(190,194,200,.5),transparent 75%),
    radial-gradient(ellipse 180px 240px at 1100px 180px,rgba(190,194,200,.5),transparent 75%),
    linear-gradient(180deg,#dfe2e6 0%,#eaecef 50%,#f0f1f3 100%)}
.field{background:var(--white);font-size:13px;color:#555;padding:17px 0 0 25px;height:49px}
.submit{top:3686px;font-size:17px;color:#222;text-decoration:underline}

/* footer */
.footer{top:3812px;left:0;width:1200px;height:306px;background:var(--navy-deep)}
.foot-bar{top:4118px;left:0;width:1200px;height:66px;background:var(--navy-bar);border-top:1px solid #27406a}
.foot-head{top:3874px;font-size:12px;color:var(--white)}
.foot-list{list-style:none;font-size:13px;line-height:27px;color:#c9d2e2}
.foot-contact{left:861px;font-size:13px;color:var(--white);display:flex;gap:14px;align-items:flex-start}
.icon{width:26px;height:26px;border-radius:50%;background:#c9d2e2;flex:none;display:flex;align-items:center;justify-content:center}
.social{top:4046px;left:866px;display:flex;gap:8px}
.social span{width:28px;height:28px;border-radius:50%;background:var(--white)}
.foot-small{top:4142px;font-size:12px;color:#a9b5ca}
</style>
</head>
<body>

<section class="abs hero" role="img" aria-label="City skyline at dusk with river and bridges"></section>
<header class="abs nav">
  <div class="abs brand"><span class="brand-dot"></span>VELOREN REAL ESTATE</div>
  <span class="abs nav-item" style="left:393px">ABOUT US ⌄</span>
  <span class="abs nav-item" style="left:503px">OUR BUSINESSES ⌄</span>
  <span class="abs nav-item" style="left:664px">INVESTORS LOBBY</span>
  <span class="abs nav-item" style="left:830px">NEWS</span>
  <span class="abs nav-item" style="left:917px">CONTACT US</span>
  <span class="abs login">LOG IN</span>
</header>
<svg class="abs play" viewBox="0 0 54 54" aria-hidden="true"><path d="M21 16 L38 27 L21 38 Z" fill="#fff"/></svg>
<h1 class="abs center display hero-title">Leading Global Private<br>Equity Real Estate</h1>
<a class="abs center display hero-link">About Us</a>

<section class="abs who" role="img" aria-label="Faded aerial view of city towers"></section>
<p class="abs center display eyebrow">Who We Are</p>
<h2 class="abs center display who-title">Veloren Real Estate</h2>
<div class="abs rule" style="left:571px;top:836px"></div>
<p class="abs who-copy">Lorem ipsum dolor sit amet, consectetur adipiscing elised do eiusmod tempor incididunt ut labore et do-loreUt enim ad minim veniam, quis nostrud exercitation ullamco laboris nisi</p>
<div class="abs who-mark"></div>
<div class="abs stat" style="left:124px;top:1044px"><div class="display stat-num">$250</div><div class="stat-label">REAL ESTATE PROJECTS</div></div>
<div class="abs stat" style="left:451px;top:1048px"><div class="display stat-num">$25B</div><div class="stat-label">PRIVATE EQUITY</div></div>
<div class="abs stat" style="left:779px;top:1048px"><div class="display stat-num">$13B</div><div class="stat-label">FUND SOLUTIONS</div></div>

<h2 class="abs center display plat-title">Our Investment Platforms</h2>
<div class="abs plat" style="left:51px;top:1397px">
  <div class="plat-photo" role="img" aria-label="Glass office tower seen from below" style="background:radial-gradient(circle at 30% 25%,#e6eef8 0%,#a9c2de 40%,#5b7fac 75%,#3c5c88 100%)"></div>
  <h3 class="display plat-name">Lorem Ipsum<br>Dolor Sit</h3>
  <p class="plat-copy">Lorem ipsum dolor sit amet, con-sectetur adipiscing elit, sed do eiusmod tempor incididunt ut co laboris nisi ut aliquip</p>
  <a class="link">Learn More</a>
</div>
<div class="abs plat" style="left:278px;top:1397px">
  <div class="plat-photo" role="img" aria-label="Hand holding tablet with private equity charts" style="background:radial-gradient(circle at 45% 60%,#c9b8c8 0%,#7d7597 35%,#3a4266 70%,#1f2745 100%)"></div>
  <h3 class="display plat-name">Lorem Ipsum<br>Dolor Sit</h3>
  <p class="plat-copy">Lorem ipsum dolor sit amet, con-sectetur adipiscing elit, sed do eiusmod tempor incididunt ut co laboris nisi ut aliquip</p>
  <a class="link">Learn More</a>
</div>
<div class="abs plat" style="left:502px;top:1397px">
  <div class="plat-photo" role="img" aria-label="Dark skyscrapers against the sky" style="background:radial-gradient(circle at 75% 20%,#e8eef5 0%,#a8b6c7 30%,#4b566b 65%,#1e2534 100%)"></div>
  <h3 class="display plat-name">Lorem Ipsum<br>Dolor Sit</h3>
  <p class="plat-copy">Lorem ipsum dolor sit amet, con-sectetur adipiscing elit, sed do eiusmod tempor incididunt ut co laboris nisi ut aliquip</p>
  <a class="link">Learn More</a>
</div>
<div class="abs plat" style="left:733px;top:1397px">
  <div class="plat-photo" role="img" aria-label="Lit building facade at night" style="background:radial-gradient(circle at 40% 40%,#56b4bd 0%,#2a7f8c 30%,#8a3f6a 60%,#151a2c 100%)"></div>
  <h3 class="display plat-name">Lorem Ipsum<br>Dolor Sit</h3>
  <p class="plat-copy">Lorem ipsum dolor sit amet, con-sectetur adipiscing elit, sed do eiusmod tempor incididunt ut co laboris nisi ut aliquip</p>
  <a class="link">Learn More</a>
</div>
<div class="abs plat" style="left:959px;top:1390px">
  <div class="plat-photo" role="img" aria-label="Glass tower reflecting clouds" style="background:radial-gradient(circle at 35% 30%,#ffffff 0%,#dfe8f2 35%,#9bb8d4 65%,#4f7ba6 100%)"></div>
  <h3 class="display plat-name" style="margin-top:35px">Lorem Ipsum<br>Dolor Sit</h3>
  <p class="plat-copy">Lorem ipsum dolor sit amet, con-sectetur adipiscing elit, sed do eiusmod tempor incididunt ut co laboris nisi ut aliquip</p>
  <a class="link">Learn More</a>
</div>

<section class="abs edge"></section>
<div class="abs edge-photo" role="img" aria-label="Black and white Manhattan skyline"></div>
<h2 class="abs display section-title" style="left:663px;top:1986px">Our Edge</h2>
<div class="abs rule" style="left:663px;top:2024px"></div>
<div class="abs body-copy" style="left:663px;top:2052px;width:460px">
  <p>Lorem ipsum dolor sit amet, consectetur adipiscing elit, sed do eiusmod tempor incididunt ut co laboris nisi ut aliquip ex ea commodo consequat. Duis aute irure dolor in reprehende</p>
  <p style="margin-top:12px">Aabor et dolore magna aliqua. Ut enim ad minim veniam, quis nostrud exercitation ullamco laboris nisi ut aliquip ex ea commodo consequat. Duis aute irure dolor</p>
</div>
<a class="abs link" style="left:663px;top:2249px;font-size:12px">Investor Information</a>

<section class="abs news" role="img" aria-label="Navy tinted city skyline"></section>
<h2 class="abs center display news-title">Stay Updated</h2>
<p class="abs center news-sub">Get our latest insights, firm announcements and Charitable Foundation updates.</p>
<div class="abs news-input">Email address</div>
<div class="abs display news-btn">Subscribe</div>

<div class="abs resp-photo" role="img" aria-label="Team gathered around a laptop in an office, black and white"></div>
<h2 class="abs display section-title" style="left:122px;top:2905px">Our Responsibility</h2>
<div class="abs rule" style="left:122px;top:2942px"></div>
<div class="abs body-copy" style="left:124px;top:2968px;width:420px">
  <p>Lorem ipsum dolor sit amet, consectetur adipiscing elit, sed do eiusmod tempor incididunt ut co laboris nisi ut aliquip ex ea commodo consequat.</p>
  <p style="margin-top:12px">Aabor et dolore magna aliqua. Ut enim ad minim veniam, quis nostrud exercitation ullamco labor</p>
</div>
<a class="abs link" style="left:133px;top:3142px;font-size:12px">Learn More</a>

<section class="abs contact" role="img" aria-label="Faded city skyline"></section>
<h2 class="abs center display section-title" style="top:3382px">Get In Touch</h2>
<div class="abs rule" style="left:563px;top:3422px;width:80px"></div>
<div class="abs field" style="left:231px;top:3456px;width:367px">First Name</div>
<div class="abs field" style="left:609px;top:3456px;width:367px">Last Name</div>
<div class="abs field" style="left:231px;top:3514px;width:367px">Phone Number</div>
<div class="abs field" style="left:609px;top:3514px;width:367px">Email address</div>
<div class="abs field" style="left:231px;top:3571px;width:745px;height:91px">Message</div>
<a class="abs center display submit">Submit Now</a>

<footer class="abs footer"></footer>
<h4 class="abs display foot-head" style="left:128px">Important Links</h4>
<ul class="abs foot-list" style="left:130px;top:3906px">
  <li>About Us</li><li>Our Businesses</li><li>Investor Lobby</li><li>News</li><li>Contact Us</li>
</ul>
<h4 class="abs display foot-head" style="left:398px">Explore Veloren Real Estate</h4>
<ul class="abs foot-list" style="left:400px;top:3909px">
  <li>Private Equity</li><li>Real Estate</li><li>Credit</li><li>Strategic Partners</li><li>Tactical Opportunities</li><li>Infrastructure</li>
</ul>
<ul class="abs foot-list" style="left:602px;top:3909px">
  <li>Insurance Solutions</li><li>Life Sciences</li><li>Portfolio Operations</li><li>Technology and Innovations</li><li>Registered Products</li>
</ul>
<h4 class="abs display foot-head" style="left:861px">Contact Details</h4>
<div class="abs foot-contact" style="top:3910px">
  <span class="icon"><svg width="14" height="16" viewBox="0 0 14 16"><path d="M7 1a5 5 0 0 1 5 5c0 4-5 9-5 9S2 10 2 6a5 5 0 0 1 5-5z" fill="#10244a"/><circle cx="7" cy="6" r="2" fill="#c9d2e2"/></svg></span>
  <span style="line-height:16px">88 Harbor Crest Ave Unit B<br>Palm Shore, FL 33000</span>
</div>
<div class="abs foot-contact" style="top:3960px;align-items:center">
  <span class="icon"><svg width="14" height="14" viewBox="0 0 14 14"><path d="M3 1l2 3-1 1.5c1 2 2.5 3.5 4.5 4.5L10 9l3 2-1.5 2.5C6 13 1 8 .5 2.5z" fill="#10244a"/></svg></span>
  <span style="font-size:14px">555-210-4187</span>
</div>
<div class="abs foot-contact" style="top:3996px;align-items:center">
  <span class="icon"><svg width="14" height="10" viewBox="0 0 14 10"><rect x="0" y="0" width="14" height="10" fill="#10244a"/><path d="M0 0l7 5 7-5" stroke="#c9d2e2" fill="none"/></svg></span>
  <span>info@velorenrealestate.com</span>
</div>
<div class="abs social"><span></span><span></span><span></span><span></span></div>
<div class="abs foot-bar"></div>
<p class="abs foot-small" style="left:126px">Copyright © 2022 Veloren Realestate</p>
<p class="abs foot-small" style="left:823px">Terms of Use &nbsp;|&nbsp; Sitemap &nbsp;|&nbsp; Privacy Policy</p>

</body>
</html>
```